KOVA! Card

The single side "business card" will be utilized to write down product information for our customers. The card needs to include our logo in josefin font and read KOVA! on the front. Our brand colors are espresso brown and copper. The back needs to be white (blank) to allow us to write information down. We want modern, bold, clean and fun.
I have attached a copy of our logo but you do not have to utilize exactly as shown.

```html
<!DOCTYPE html>
<html lang="en">
<head>
<meta charset="utf-8">
<title>KOVA! Card</title>
<link rel="stylesheet" href="https://fonts.googleapis.com/css2?family=Josefin+Sans:wght@300;400&display=swap">
<style>
  :root {
    --espresso: #372820;
    --copper: #a6602d;
    --paper: #e9e9e9;
    --ink-grey: #4a4a4a;
    --backdrop: #c4c4c4;
  }
  * { margin: 0; padding: 0; box-sizing: border-box; }
  html, body {
    width: 1200px;
    height: 900px;
    overflow: hidden;
    background: var(--backdrop);
  }
  .sheet {
    position: relative;
    width: 1200px;
    height: 900px;
    display: grid;
    grid-template-columns: 480px 480px;
    grid-template-rows: 274px 274px;
    gap: 60px;
    justify-content: center;
    align-content: center;
  }
  .card {
    position: relative;
    width: 480px;
    height: 274px;
    font-family: "Josefin Sans", sans-serif;
  }
  .card--front {
    display: flex;
    align-items: center;
    justify-content: center;
  }
  .card--copper { background: var(--copper); }
  .card--espresso { background: var(--espresso); }
  .card--back {
    background: var(--paper);
  }
  .headline {
    font-size: 96px;
    font-weight: 300;
    letter-spacing: 10px;
    line-height: 1;
    padding-top: 14px;
  }
  .card--copper .headline { color: var(--espresso); }
  .card--espresso .headline { color: var(--copper); }
  .wordmark {
    position: absolute;
    top: 40px;
    right: 48px;
    text-align: left;
    color: var(--ink-grey);
  }
  .wordmark__name {
    display: block;
    font-size: 40px;
    font-weight: 300;
    letter-spacing: 3px;
    line-height: 1;
  }
  .wordmark__tagline {
    display: block;
    font-size: 11px;
    font-weight: 400;
    letter-spacing: 0.5px;
    margin-top: 2px;
  }
</style>
</head>
<body>
  <main class="sheet">
    <section class="card card--back">
      <div class="wordmark">
        <span class="wordmark__name">brantels</span>
        <span class="wordmark__tagline">Jewelry &amp; Design Studio</span>
      </div>
    </section>
    <section class="card card--front card--copper">
      <p class="headline">KOVA!</p>
    </section>
    <section class="card card--front card--espresso">
      <p class="headline">KOVA!</p>
    </section>
    <section class="card card--back">
      <div class="wordmark">
        <span class="wordmark__name">brantels</span>
        <span class="wordmark__tagline">Jewelry &amp; Design Studio</span>
      </div>
    </section>
  </main>
</body>
</html>
```